Business Card Design Project

We are rebranding an existing automotive collision repair business. The business is called dent haven. I have attached logo but I'm not tied to that. I want to leave this wide open.

I want this card to say we are professional, competent, cutting edge. We are focused on customers and use a lot of the latest technology to make the customer experience different. We sign customers in on iPads. Paperwork I signed electronically and updates are sent via text, email, logging on a website or as they wish. I want this innovation and image to come through in our cards

Target Market(s)

60%. Women 40% men. Age 35-60

Industry/Entity Type

Automotive

Requirements
Must have
• The card must have name, title, phone,email, cell, web page

```html
<!DOCTYPE html>
<html lang="en">
<head>
<meta charset="UTF-8">
<title>Dent Haven — Business Card</title>
<link href="https://fonts.googleapis.com/css2?family=Arimo:wght@400;700&display=swap" rel="stylesheet">
<style>
  :root {
    --stage: #e6e7e9;
    --card-dark: #38373c;
    --card-light: #ffffff;
    --brand-green: #64803a;
    --brand-green-text: #5f7e3a;
    --ink: #1d1d1f;
    --muted: #a2a2a2;
    --icon: #a8a8a8;
    --shadow: rgba(0, 0, 0, 0.35);
  }
  * { margin: 0; padding: 0; box-sizing: border-box; }
  html, body {
    width: 1200px; height: 800px; overflow: hidden;
    background: var(--stage);
    font-family: "Arimo", Arial, sans-serif;
  }
  .stage { position: relative; width: 1200px; height: 800px; }
  .card {
    position: absolute; top: 122px;
    width: 282px; height: 492px;
    border-radius: 14px; overflow: hidden;
    box-shadow: 3px 5px 6px var(--shadow);
  }
  .card--front { left: 208px; background: var(--card-dark); }
  .card--back { left: 692px; background: var(--card-light); }

  .brand-band {
    position: absolute; left: 40px; top: 284px;
    width: 242px; height: 82px;
    background: var(--brand-green);
    border-radius: 41px 0 0 41px;
    display: flex; align-items: center; justify-content: center;
  }
  .brand-name {
    color: #ffffff; font-weight: 700; font-size: 25px;
    letter-spacing: 0.3px;
  }
  .front-web {
    position: absolute; left: 0; right: 0; top: 367px;
    text-align: center; padding-left: 40px;
    color: var(--brand-green-text); font-size: 15px;
  }

  .name-tab {
    position: absolute; left: 0; top: 284px;
    width: 41px; height: 82px;
    background: var(--brand-green);
    border-radius: 0 41px 41px 0;
  }
  .person { position: absolute; left: 62px; top: 308px; }
  .person-name { color: var(--ink); font-weight: 700; font-size: 19px; line-height: 22px; }
  .person-title { color: var(--brand-green-text); font-size: 15px; line-height: 18px; }

  .contact-list { position: absolute; left: 60px; top: 374px; list-style: none; }
  .contact-item {
    display: flex; align-items: center;
    height: 26px; color: var(--muted); font-size: 15.5px;
  }
  .contact-icon { width: 20px; height: 20px; margin-right: 11px; flex: none; }
  .contact-icon * { fill: none; stroke: var(--icon); stroke-width: 1.3; }
</style>
</head>
<body>
<main class="stage">
  <section class="card card--front" aria-label="Card front">
    <div class="brand-band">
      <span class="brand-name">Dent Haven</span>
    </div>
    <p class="front-web">www.denthaven.com</p>
  </section>

  <section class="card card--back" aria-label="Card back">
    <div class="name-tab"></div>
    <div class="person">
      <p class="person-name">Mark Ellison</p>
      <p class="person-title">Director</p>
    </div>
    <ul class="contact-list">
      <li class="contact-item">
        <svg class="contact-icon" viewBox="0 0 20 20"><rect x="2" y="5" width="16" height="11"/><path d="M2 5l8 6 8-6"/></svg>
        mark@denthaven.com
      </li>
      <li class="contact-item">
        <svg class="contact-icon" viewBox="0 0 20 20"><circle cx="10" cy="10" r="8"/><ellipse cx="10" cy="10" rx="3.5" ry="8"/><path d="M2 10h16M3.5 6h13M3.5 14h13"/></svg>
        www.denthaven.com
      </li>
      <li class="contact-item">
        <svg class="contact-icon" viewBox="0 0 20 20"><path d="M5 2.5l3 3.5-2 2c1 2.5 3 4.5 5.5 5.5l2-2 3.5 3-2 2.5C9 16.5 3.5 11 2.5 4.5z"/></svg>
        +1 (555) 014-2387
      </li>
      <li class="contact-item">
        <svg class="contact-icon" viewBox="0 0 20 20"><rect x="6" y="2" width="8" height="16" rx="1.5"/><path d="M9 15.5h2"/></svg>
        +1 (555) 014-2387
      </li>
    </ul>
  </section>
</main>
</body>
</html>
```